Redesign a Start-Up Dating Website

Website: https://morvelique.com.
Make sure the design has an island style theme.
I would like the 7 pages of my website to have a new and professional look. I want the same colors to remain, but I want a creative look for all the pages. This is a dating website that is in the startup stage. So, I want to give my entire website a custom makeover. I want something that will stand out from the other dating sites. Something that will attract more people to want to use my services, and hopefully get new members.
Target Market(s)
Dating
Industry/Entity Type
Dating
Coding
Coded - Design and coding required
Number of Pages Required
5+ page
Font styles to use
Other font styles liked:
- Decorative, San Serif
Requirements
Must have
- The design must have the original colors and a stylish font to go along. The design must be creative, welcoming, and professional. I would like an island style theme for the website. This is a dating website so make sure that the design is tailored to that aspect.
Nice to have
- It would be nice to have a decorative font and a professional style on all the pages. Make sure the design will be mobile responsive and friendly for all the pages on the website.
Should not have
- The design should not be bland and uncreative.

```html
<!DOCTYPE html>
<html lang="en">
<head>
<meta charset="utf-8">
<title>About – Morvelique</title>
<link rel="stylesheet" href="https://fonts.googleapis.com/css2?family=Raleway:wght@500;600;700&family=Open+Sans:ital,wght@0,400;0,600;1,400&display=swap">
<style>
:root{
  --teal:#4fb99a;
  --teal-deep:#3aa589;
  --orange:#f08a1c;
  --ink:#1f1f1f;
  --body:#6a6a6a;
  --rule:#c9c9c9;
  --footer-bg:#efefef;
  --white:#ffffff;
  --fb:#3b5998;
  --in:#0e76a8;
  --tw:#1da1f2;
}
*{margin:0;padding:0;box-sizing:border-box}
html,body{width:677px;height:1200px;overflow:hidden;background:var(--white)}
body{position:relative;font-family:"Open Sans",Arial,sans-serif;color:var(--body)}
.abs{position:absolute}
.accent-line{height:3px;background:linear-gradient(90deg,var(--teal),#9bb26a,var(--orange))}

/* header */
.site-header{top:0;left:0;width:677px;height:52px;background:var(--white);box-shadow:0 2px 4px rgba(0,0,0,.12);z-index:2}
.site-header .accent-line{position:absolute;top:0;left:0;right:0;height:2px}
.brand{left:55px;top:10px;display:flex;align-items:center;gap:5px}
.brand-dot{width:30px;height:30px;border-radius:50%;background:var(--orange)}
.brand-name{font-family:"Raleway",sans-serif;font-weight:700;font-size:20px;color:var(--teal)}
.main-nav{left:214px;top:20px;display:flex;gap:14.5px;font-family:"Raleway",sans-serif;font-weight:600;font-size:9.2px;color:var(--ink)}
.main-nav .current{color:var(--orange)}
.login-btn{left:564px;top:14px;width:57px;height:24px;border-radius:12px;background:var(--orange);color:var(--white);font-family:"Raleway",sans-serif;font-weight:700;font-size:9.2px;display:flex;align-items:center;justify-content:center;gap:4px}

/* hero */
.hero{top:52px;left:0;width:677px;height:160px;background:linear-gradient(180deg,#6b6d92 0%,#8e7f9c 45%,#a98e9e 62%,#5b6e8a 78%,#4a5a78 100%)}
.hero-title{top:52px;left:0;width:677px;height:160px;display:flex;align-items:center;justify-content:center;font-family:"Raleway",sans-serif;font-weight:600;font-size:38px;color:var(--white);letter-spacing:.5px}

/* breadcrumb */
.breadcrumb{left:55px;top:223px;font-family:"Raleway",sans-serif;font-weight:600;font-size:8.4px;color:var(--ink)}
.breadcrumb .sep{margin:0 5px}
.breadcrumb .here{color:var(--orange)}
.rule{left:55px;top:243px;width:566px;height:1px;background:var(--rule)}

/* founder */
.founder-photo{left:55px;top:292px;width:190px;height:219px;border:1px solid #ddd;padding:3px;background:var(--white)}
.founder-photo div{width:100%;height:100%;background:linear-gradient(180deg,#eceaea 0%,#e3e0df 40%,#2e3648 70%,#1e2535 100%)}
.founder-bio{left:282px;top:284px;width:340px}
.founder-name{font-family:"Raleway",sans-serif;font-weight:700;font-size:17px;color:var(--ink)}
.founder-role{font-family:"Raleway",sans-serif;font-weight:500;font-size:11px;color:var(--orange);margin-top:2px}
.founder-bio p{font-size:7.5px;line-height:16.4px;margin-top:8px}
.founder-bio p + p{margin-top:16px}
.founder-email{display:flex;align-items:center;gap:7px;margin-top:12px;font-size:9.5px;color:var(--ink)}
.socials{display:flex;gap:4px;margin-top:12px}
.socials span{width:22px;height:22px;border-radius:50%}

/* signup */
.signup{top:680px;left:0;width:677px;height:188px;background:linear-gradient(90deg,#56bd9d 0%,#4cb497 60%,#44a88f 100%)}
.signup-title{top:712px;left:0;width:677px;text-align:center;font-family:"Raleway",sans-serif;font-weight:600;font-size:22px;color:var(--white)}
.signup-text{top:747px;left:130px;width:417px;text-align:center;font-size:8px;line-height:16.5px;color:var(--white)}
.signup-form{top:796px;left:158px;display:flex}
.signup-input{width:289px;height:32px;background:var(--white);font-size:8px;color:#444;padding-left:12px;display:flex;align-items:center}
.signup-btn{width:72px;height:32px;background:var(--orange);color:var(--white);font-family:"Raleway",sans-serif;font-weight:700;font-size:9.5px;display:flex;align-items:center;justify-content:center}

/* quote */
.quote-mark{top:905px;left:313px}
.quote-text{top:968px;left:110px;width:457px;text-align:center;font-style:italic;font-size:8px;line-height:16.5px;color:#5f5f5f}

/* footer */
.site-footer{top:1061px;left:0;width:677px;height:139px;background:var(--footer-bg)}
.site-footer .accent-line{height:3px}
.contact-item{display:flex;align-items:center;gap:10px;font-size:7.8px;color:#555;line-height:13.5px}
.ring{width:25px;height:25px;border-radius:50%;border:1px solid #b9b9b9;display:flex;align-items:center;justify-content:center;flex:none}
.footer-links{top:1129px;left:0;width:677px;text-align:center;font-size:8px;color:#666}
.footer-links i{font-style:normal;margin:0 5px}
.footer-rule{top:1157px;left:55px;width:566px;height:1px;background:#d5d5d5}
.copyright{top:1172px;left:56px;font-size:7px;color:#666}
.footer-social{top:1168px;left:552px;display:flex;gap:4px}
.footer-social span{width:22px;height:22px;border-radius:50%;border:1px solid var(--orange)}
</style>
</head>
<body>

<header class="site-header abs">
  <div class="accent-line"></div>
  <div class="brand abs"><span class="brand-dot"></span><span class="brand-name">Morvelique</span></div>
  <nav class="main-nav abs">
    <span>HOME</span><span>SEARCH</span><span>MEMBERS</span><span>EXTRAS</span><span class="current">ABOUT</span><span>PREMIUM</span><span>CONTACT</span>
  </nav>
  <div class="login-btn abs">
    <svg width="7" height="8" viewBox="0 0 7 8"><rect x="0" y="3.5" width="7" height="4.5" rx=".6" fill="#fff"/><path d="M1.6 3.6V2.4a1.9 1.9 0 0 1 3.8 0v1.2" fill="none" stroke="#fff" stroke-width="1.1"/></svg>
    LOGIN
  </div>
</header>

<div class="hero abs" role="img" aria-label="Couple holding hands on a beach at sunset"></div>
<h1 class="hero-title abs">ABOUT</h1>

<div class="breadcrumb abs">HOME<span class="sep">&gt;&gt;</span><span class="here">ABOUT</span></div>
<div class="rule abs"></div>

<figure class="founder-photo abs"><div role="img" aria-label="Portrait of the founder in a dark suit"></div></figure>

<section class="founder-bio abs">
  <h2 class="founder-name">DANA WHITFIELD</h2>
  <div class="founder-role">FOUNDER</div>
  <p>Morvelique aims to provide a straight-forward, easy-to-use online dating service. I won't over-complicate things or reduce the amount of people you can talk to with algorithms. I know that sometimes, opposites attract and sparks can fly with the last person you thought you'd be interested in-so I won't hide anybody from you.There is no discrimination on this dating site, it's not only about accepting young singles. I think everybody deserves love and should be given the same opportunity to find their true match. Especially when it comes to finding your perfect match, a broader community is always better. My trusted 24-hour service means that there are singles online at all times whether you're a night-owl or a morning person, there's always someone to connect with.</p>
  <p>I created Morvelique to provide an affordable, comfortable, and enjoyable online dating experience. Online dating should not be complicated and expensive. I want members to use my dating site with ease when looking for a potential love match. I hope you have a great time here at Morvelique and hopefully find your soulmate.</p>
  <div class="founder-email">
    <svg width="10" height="8" viewBox="0 0 10 8"><rect width="10" height="8" rx="1" fill="var(--orange)"/><path d="M.5 1l4.5 3.2L9.5 1" fill="none" stroke="#fff" stroke-width="1"/></svg>
    dwf@morvelique.com
  </div>
  <div class="socials"><span style="background:var(--fb)"></span><span style="background:var(--in)"></span><span style="background:var(--tw)"></span></div>
</section>

<section class="signup abs" role="img" aria-label="Couple dining by the sea, teal tinted"></section>
<h2 class="signup-title abs">START MORVELIQUING WITH FREE SIGNUP</h2>
<p class="signup-text abs">Morvelique aims to provide a straight-forward, easy-to-use online dating service. I won't over-complicate things or reduce the amount of people you can talk to with algorithms. Read More</p>
<div class="signup-form abs"><div class="signup-input">Email Address</div><div class="signup-btn">SIGN UP</div></div>

<svg class="quote-mark abs" width="50" height="40" viewBox="0 0 50 40"><g fill="var(--orange)"><circle cx="11" cy="29" r="10"/><path d="M2 28C2 14 9 4 20 1l2 4C14 9 11 16 12 22z"/><circle cx="37" cy="29" r="10"/><path d="M28 28C28 14 35 4 46 1l2 4C40 9 37 16 38 22z"/></g></svg>
<p class="quote-text abs">“I know that dating sites can be scary, so I offer a money-back guarantee payment within your first month as a premium member. If you find Morvelique is not for you, after all, I won't be upset with you. It's easy to sign-up, so it should be easy to leave- whether it's because you've found true love, or just need a break, I understand.”</p>

<footer class="site-footer abs">
  <div class="accent-line"></div>
</footer>
<div class="contact-item abs" style="top:1087px;left:129px">
  <span class="ring"><svg width="8" height="11" viewBox="0 0 8 11"><path d="M4 0a4 4 0 0 1 4 4c0 3-4 7-4 7S0 7 0 4a4 4 0 0 1 4-4z" fill="var(--orange)"/><circle cx="4" cy="4" r="1.4" fill="#fff"/></svg></span>
  <span>Morvelique Dating<br>Contact | Morvelique | Dating Easy</span>
</div>
<div class="contact-item abs" style="top:1087px;left:315px">
  <span class="ring"><svg width="10" height="10" viewBox="0 0 10 10"><path d="M2 0l2 2.5-1 1.3c.7 1.4 1.8 2.5 3.2 3.2L7.5 6 10 8 8.6 9.8C4 9.5.5 6 .2 1.4z" fill="var(--orange)"/></svg></span>
  <span>1 555 010 0199</span>
</div>
<div class="contact-item abs" style="top:1087px;left:431px">
  <span class="ring"><svg width="10" height="8" viewBox="0 0 10 8"><rect width="10" height="8" rx="1" fill="var(--orange)"/><path d="M.5 1l4.5 3.2L9.5 1" fill="none" stroke="#fff" stroke-width="1"/></svg></span>
  <span>contact@morvelique.com</span>
</div>
<nav class="footer-links abs">Morvelique<i>|</i>About<i>|</i>Contact<i>|</i>Login<i>|</i>Members<i>|</i>Premium<i>|</i>Register<i>|</i>Search</nav>
<div class="footer-rule abs"></div>
<div class="copyright abs">Copyrights © 2017, Morvelique. All rights reserved.</div>
<div class="footer-social abs"><span></span><span></span><span></span></div>

</body>
</html>
```